Custom hot rod builder needs a website for launch of new business where he will build luxury garages

We need a website that gives a WOW first impression for "Summit Carports". This is a new business so photos are renderings but we need it to really attract a particular audience. Our initial business is custom hot rods so now we are building garages for them. These will be like luxury "homes" for cars! I will attach our new logo. Website needs to feel powerful and prestigious.

Target Market(s)

middle aged men, car enthusiasts

Industry/Entity Type

automotive, construction

Coding

Coded - Design and coding required

Number of Pages Required

2 page

Font styles to use
Serif

Colors
0054AA
0677BA
7BADD7
CADEEF
E8F1F8

Requirements
Must have
• a WOW factor. luxury. contact form.
Nice to have
• ?

```html
<!DOCTYPE html>
<html lang="en">
<head>
<meta charset="utf-8">
<title>Summit Carports</title>
<link href="https://fonts.googleapis.com/css2?family=Michroma&family=Oswald:wght@500;600&family=Mulish:ital,wght@0,400;0,600;0,700;0,800;1,400&display=swap" rel="stylesheet">
<style>
:root{
  --blue-deep:#0054AA;
  --blue:#0677BA;
  --blue-soft:#7BADD7;
  --blue-pale:#CADEEF;
  --blue-mist:#E8F1F8;
  --cta:#1ea0df;
  --black:#000;
  --white:#fff;
  --grey-text:#4a4a4a;
  --submit:#6e0a0a;
  --star:#f5b400;
}
*{margin:0;padding:0;box-sizing:border-box}
html,body{width:1200px;height:4574px;overflow:hidden;background:var(--black)}
body{position:relative;font-family:'Mulish',sans-serif;color:var(--white)}
.abs{position:absolute}
.btn{position:absolute;background:var(--cta);color:var(--white);font-family:'Mulish',sans-serif;font-size:16px;display:flex;align-items:center;justify-content:center;border-radius:2px}
.section-title{position:absolute;left:0;width:1200px;text-align:center;font-family:'Michroma',sans-serif;font-variant:small-caps;letter-spacing:5px;font-size:34px;color:var(--blue)}
.section-title::after{content:"";display:block;width:110px;height:2px;background:var(--blue-soft);margin:10px auto 0}
.photo{position:absolute}

/* hero */
.hero{left:0;top:0;width:1200px;height:643px;background:linear-gradient(180deg,#3a2618 0%,#6b4a2c 35%,#8a6a44 60%,#3c3c3a 100%)}
.hero-shade{left:0;top:0;width:1200px;height:643px;background:radial-gradient(ellipse at 30% 80%,rgba(40,110,110,.55),transparent 45%),radial-gradient(ellipse at 80% 85%,rgba(170,40,30,.45),transparent 40%)}
.brand{left:186px;top:26px;display:flex;align-items:center;gap:12px;font-family:'Mulish',sans-serif;font-weight:800;font-size:28px;color:var(--white)}
.brand-dot{width:40px;height:40px;border-radius:50%;background:var(--blue)}
.nav{left:576px;top:32px;display:flex;gap:28px;font-size:15px;align-items:center}
.nav a{color:var(--white);text-decoration:none}
.nav .active{color:var(--cta);border-bottom:2px solid var(--cta);padding-bottom:6px}
.nav .phone{display:flex;gap:8px;align-items:center;color:var(--cta);font-size:21px;margin-left:6px}
.hero-title{left:0;width:1200px;top:208px;text-align:center;font-family:'Oswald',sans-serif;font-weight:600;font-size:40px;color:var(--white);text-shadow:0 2px 6px rgba(0,0,0,.6)}
.hero-arrow{width:36px;height:36px;border:2px solid var(--white);border-radius:50%;display:flex;align-items:center;justify-content:center}

/* welcome */
.welcome-title{left:190px;top:722px;font-family:'Michroma',sans-serif;font-variant:small-caps;font-size:30px;letter-spacing:5px;line-height:32px;color:var(--blue)}
.welcome-title::after{content:"";display:block;width:100px;height:2px;background:var(--blue-soft);margin-top:8px}
.welcome-text{left:190px;top:812px;width:450px;font-size:12.5px;line-height:23px;color:#e6e6e6}
.welcome-text p{margin-bottom:8px}
.welcome-ring{left:656px;top:706px;width:356px;height:356px;border-radius:50%;background:var(--blue-soft)}
.welcome-photo{left:670px;top:720px;width:328px;height:328px;border-radius:50%;background:linear-gradient(180deg,#c9d9e6 0%,#9fb7a3 45%,#7f8a86 70%,#d8dde0 100%)}

/* offer cards */
.card{position:absolute;top:1205px;width:195px;height:240px;background:var(--blue-mist);text-align:center;color:#222}
.card svg{margin-top:30px}
.card h3{font-size:13.5px;font-weight:600;margin-top:14px}
.card p{font-size:11px;line-height:20px;color:var(--grey-text);margin:8px 14px 0}

/* banners */
.banner{left:0;width:1200px;height:491px;background:linear-gradient(180deg,#2a2f33 0%,#3b4247 40%,#2a2c2c 75%,#1a1d1a 100%)}
.banner-shade{left:0;width:1200px;height:491px;background:rgba(0,0,0,.35)}
.banner-text{left:0;width:1200px;text-align:center;font-family:'Michroma',sans-serif;font-variant:small-caps;font-size:30px;letter-spacing:6px;line-height:42px;color:var(--white)}

/* gallery */
.tile{position:absolute;width:263px;height:260px;border:1px solid #333;background:#fff}
.tile .pic{width:100%;height:221px}
.tile .cap{height:39px;display:flex;align-items:center;justify-content:center;font-size:12.5px;color:#333;background:#f4f4f4}
.tile.is-active .cap{background:var(--blue-deep);color:var(--white)}

/* reviews */
.quote-badge{left:578px;top:3006px;width:44px;height:44px;border-radius:50%;background:var(--cta);display:flex;align-items:center;justify-content:center;font-family:Georgia,serif;font-size:30px;font-weight:700;line-height:1;padding-top:12px}
.review-text{left:230px;top:3060px;width:740px;text-align:center;font-style:italic;font-size:12.5px;line-height:23px;color:#e6e6e6}
.review-name{left:0;width:1200px;top:3144px;text-align:center;font-size:15px}
.review-stars{left:0;width:1200px;top:3168px;text-align:center;color:var(--star);font-size:14px;letter-spacing:2px}

/* inquiry */
.footer-band{left:0;top:4132px;width:1200px;height:442px;background:var(--blue-deep)}
.inquiry{left:275px;top:3813px;width:648px;height:444px;background:var(--blue-mist);border:6px solid #5a5f66}
.inquiry h2{position:absolute;left:0;width:100%;top:60px;text-align:center;font-family:'Michroma',sans-serif;font-variant:small-caps;font-size:28px;letter-spacing:5px;color:var(--blue)}
.field{position:absolute;background:var(--white);border:1px solid #dfe6ee;font-size:10.5px;color:#444;display:flex;align-items:center;gap:7px;padding-left:12px}
.field.area{align-items:flex-start;padding-top:12px}
.submit{position:absolute;left:262px;top:340px;width:112px;height:32px;background:var(--submit);color:var(--white);font-size:11px;font-weight:800;letter-spacing:1px;display:flex;align-items:center;justify-content:center}

/* footer */
.foot-brand{left:0;width:1200px;top:4298px;display:flex;justify-content:center;align-items:center;gap:12px;font-weight:800;font-size:30px}
.foot-brand .brand-dot{background:var(--white)}
.contact{position:absolute;top:4398px;display:flex;gap:16px;align-items:center;font-size:13.5px;line-height:20px}
.contact .ring{width:42px;height:42px;border:1.5px solid var(--white);border-radius:50%;display:flex;align-items:center;justify-content:center}
.socials{left:0;width:1200px;top:4493px;display:flex;justify-content:center;gap:14px}
.socials span{width:26px;height:26px;border:1.5px solid var(--white);border-radius:50%}
.copyright{left:0;width:1200px;top:4537px;text-align:center;font-size:12.5px}
</style>
</head>
<body>

<!-- hero -->
<div class="photo hero abs" role="img" aria-label="Rendering of a luxury garage interior with classic hot rods on a wooden floor"></div>
<div class="hero-shade abs"></div>
<div class="brand abs"><span class="brand-dot"></span>Summit Carports</div>
<nav class="nav abs">
  <a class="active">Home</a>
  <a>Work Gallery</a>
  <a>Contact Us</a>
  <span class="phone">
    <svg width="20" height="20" viewBox="0 0 24 24" fill="none" stroke="currentColor" stroke-width="1.8"><path d="M5 3h4l2 5-2.5 1.5a11 11 0 0 0 6 6L16 13l5 2v4a2 2 0 0 1-2 2A17 17 0 0 1 3 5a2 2 0 0 1 2-2z"/></svg>
    555.201.4480
  </span>
</nav>
<h1 class="hero-title abs">We Build Custom Hot Rod Luxury Garages</h1>
<div class="btn" style="left:523px;top:269px;width:152px;height:39px">Contact Us Today</div>
<div class="hero-arrow abs" style="left:89px;top:348px"><svg width="12" height="12" viewBox="0 0 12 12"><path d="M8 1 3 6l5 5" fill="none" stroke="#fff" stroke-width="1.8"/></svg></div>
<div class="hero-arrow abs" style="left:1079px;top:348px"><svg width="12" height="12" viewBox="0 0 12 12"><path d="M4 1l5 5-5 5" fill="none" stroke="#fff" stroke-width="1.8"/></svg></div>

<!-- welcome -->
<h2 class="welcome-title abs">Welcome To<br>Summit Carports</h2>
<div class="welcome-text abs">
  <p>Lorem ipsum dolor sit amet, consectetuer adipiscing elit, sed dim nonummy nibh euismod tincidunt ut laoreet dolore magna aliquam erat volutpat. Ut wisi enim ad minim veniam, quis nostrud exerci.</p>
  <p>Lorem ipsum dolor sit amet, consectetuer adipiscing elit, sed dim nonummy nibh euismod tincidunt ut laoreet dolore magna aliquam erat volutpat. Ut wisi enim ad minim veniam, quis nostrud exerci tation ullamcorper suscipit lobortis nisl ut aliquip ex ea commodo consequat. Duis aute</p>
</div>
<div class="btn" style="left:188px;top:996px;width:126px;height:42px">Contact Us</div>
<div class="welcome-ring abs"></div>
<div class="photo welcome-photo abs" role="img" aria-label="Rendering of a modern glass garage building with classic cars inside"></div>

<!-- offer -->
<h2 class="section-title" style="top:1130px">What We Offer</h2>
<div class="card" style="left:188px">
  <svg width="56" height="44" viewBox="0 0 56 44" fill="none" stroke="#0677BA" stroke-width="2"><path d="M2 12l10-6 8 4 8-4 8 4 8-4 10 6-8 14-8 6-8 4-8-4-8-6z"/><path d="M20 10l10 10 4-2"/></svg>
  <h3>Best Design Promise</h3>
  <p>Ut wisi enim ad minim veniam, queis nostrud exercitation ullamcorper let suscipit lobortis nisl ut aliquip commodo.</p>
</div>
<div class="card" style="left:398px">
  <svg width="56" height="44" viewBox="0 0 56 44" fill="none" stroke="#0677BA" stroke-width="2"><path d="M30 4h18v18L24 42 10 28z"/><circle cx="40" cy="12" r="3"/></svg>
  <h3>Always The Best Value</h3>
  <p>Ut wisi enim ad minim veniam, queis nostrud exercitation ullamcorper let suscipit lobortis nisl ut aliquip commodo.</p>
</div>
<div class="card" style="left:607px">
  <svg width="56" height="44" viewBox="0 0 56 44" fill="none" stroke="#0677BA" stroke-width="2"><circle cx="28" cy="18" r="15"/><circle cx="28" cy="18" r="10"/><path d="M28 12l2 4 4 .5-3 3 1 4-4-2-4 2 1-4-3-3 4-.5z"/><path d="M20 31l-3 11 6-3 5 4M36 31l3 11-6-3"/></svg>
  <h3>20 Years Experience</h3>
  <p>Ut wisi enim ad minim veniam, queis nostrud exercitation ullamcorper let suscipit lobortis nisl ut aliquip commodo.</p>
</div>
<div class="card" style="left:817px">
  <svg width="56" height="44" viewBox="0 0 56 44" fill="none" stroke="#0677BA" stroke-width="2"><path d="M12 24v-4a16 16 0 0 1 32 0v4"/><rect x="8" y="22" width="7" height="12" rx="2"/><rect x="41" y="22" width="7" height="12" rx="2"/><path d="M44 34c0 5-6 7-12 7"/><text x="21" y="28" font-size="11" fill="#0677BA" stroke="none" font-family="Mulish">24</text></svg>
  <h3>24 Hour Customer Service</h3>
  <p>Ut wisi enim ad minim veniam, queis nostrud exercitation ullamcorper let suscipit lobortis nisl ut aliquip commodo.</p>
</div>
<div class="btn" style="left:526px;top:1475px;width:150px;height:41px">Contact Us Today</div>

<!-- banner one -->
<div class="photo banner abs" style="top:1589px" role="img" aria-label="Night rendering of a glass-fronted garage showroom with classic cars"></div>
<div class="banner-shade abs" style="top:1589px"></div>
<div class="banner-text abs" style="top:1742px">To Build Your<br>Luxury “Homes” For Cars!</div>
<div class="btn" style="left:525px;top:1851px;width:150px;height:41px">Contact Us Today</div>

<!-- gallery -->
<h2 class="section-title" style="top:2152px">Work Gallery</h2>
<div class="tile is-active" style="left:186px;top:2224px"><div class="pic" role="img" aria-label="Two red and black hot rods in a workshop" style="background:linear-gradient(180deg,#6b5a4a,#7a3a32 55%,#b9c3d0)"></div><div class="cap">Project 1 @ Harbor Point, Denver</div></div>
<div class="tile" style="left:468px;top:2224px"><div class="pic" role="img" aria-label="Garage interior rendering with classic cars" style="background:linear-gradient(180deg,#3b2718,#8a6a44 55%,#2f5a55)"></div><div class="cap">Project 2 @ Harbor Point, Denver</div></div>
<div class="tile" style="left:751px;top:2224px"><div class="pic" role="img" aria-label="Hot rod workshop with yellow and black cars" style="background:linear-gradient(180deg,#5b5a58,#4a4740 55%,#8a8378)"></div><div class="cap">Project 3 @ Harbor Point, Denver</div></div>
<div class="tile" style="left:186px;top:2516px"><div class="pic" role="img" aria-label="Vintage blue touring car in a showroom" style="background:linear-gradient(180deg,#a07a5a,#3a3f5a 55%,#c8c4bc)"></div><div class="cap">Project 4 @ Harbor Point, Denver</div></div>
<div class="tile" style="left:468px;top:2516px"><div class="pic" role="img" aria-label="Row of hot rods in a dark garage" style="background:linear-gradient(180deg,#1e1e1e,#4a4420 55%,#2a2a2a)"></div><div class="cap">Project 5 @ Harbor Point, Denver</div></div>
<div class="tile" style="left:751px;top:2516px"><div class="pic" role="img" aria-label="Custom hot rod in a large workshop" style="background:linear-gradient(180deg,#6d6a66,#3a3634 55%,#5e5a56)"></div><div class="cap">Project 6 @ Harbor Point, Denver</div></div>
<div class="btn" style="left:527px;top:2815px;width:126px;height:41px">View All</div>

<!-- reviews -->
<h2 class="section-title" style="top:2930px">Happy Customer Reviews</h2>
<div class="quote-badge abs">“</div>
<svg class="abs" style="left:162px;top:3082px" width="16" height="26" viewBox="0 0 16 26"><path d="M14 1 2 13l12 12" fill="none" stroke="#fff" stroke-width="1.8"/></svg>
<svg class="abs" style="left:1024px;top:3082px" width="16" height="26" viewBox="0 0 16 26"><path d="M2 1l12 12L2 25" fill="none" stroke="#fff" stroke-width="1.8"/></svg>
<p class="review-text abs">Lorem ipsum dolor sit amet, consectetuer adipiscing elit, sed dim nonummy nibh euismod tincidunt ut laoreet dore magna aliquam erat volutpat. Ut wisi enim ad minim veniam, quis nostrud exerci tation ullamcorper suscipit lobortis nisl ut aliquip ex ea commodo consequat. Duis aute</p>
<div class="review-name abs">Dana Morrow</div>
<div class="review-stars abs">★★★★★</div>

<!-- banner two -->
<div class="photo banner abs" style="top:3248px" role="img" aria-label="Night rendering of a glass-fronted garage showroom with classic cars"></div>
<div class="banner-shade abs" style="top:3248px"></div>
<div class="banner-text abs" style="top:3422px">To Build Your<br>Luxury custom hot rods Garages!</div>
<div class="btn" style="left:525px;top:3517px;width:150px;height:41px">Contact Us Today</div>

<!-- inquiry -->
<div class="footer-band abs"></div>
<form class="inquiry abs">
  <h2>Quick Inquiry</h2>
  <div class="field" style="left:65px;top:113px;width:246px;height:38px">
    <svg width="11" height="11" viewBox="0 0 12 12" fill="none" stroke="#7BADD7"><circle cx="6" cy="4" r="2.5"/><path d="M1.5 11a4.5 4.5 0 0 1 9 0"/></svg>First Name</div>
  <div class="field" style="left:327px;top:113px;width:247px;height:38px">
    <svg width="11" height="11" viewBox="0 0 12 12" fill="none" stroke="#7BADD7"><circle cx="6" cy="4" r="2.5"/><path d="M1.5 11a4.5 4.5 0 0 1 9 0"/></svg>Last Name</div>
  <div class="field" style="left:65px;top:162px;width:246px;height:38px">
    <svg width="11" height="11" viewBox="0 0 12 12" fill="none" stroke="#7BADD7"><rect x="1" y="2.5" width="10" height="7"/><path d="M1 3l5 4 5-4"/></svg>Email</div>
  <div class="field" style="left:327px;top:162px;width:247px;height:38px">
    <svg width="11" height="11" viewBox="0 0 24 24" fill="none" stroke="#7BADD7" stroke-width="2"><path d="M5 3h4l2 5-2.5 1.5a11 11 0 0 0 6 6L16 13l5 2v4a2 2 0 0 1-2 2A17 17 0 0 1 3 5a2 2 0 0 1 2-2z"/></svg>Phone</div>
  <div class="field area" style="left:65px;top:210px;width:509px;height:89px">
    <svg width="11" height="11" viewBox="0 0 12 12" fill="none" stroke="#7BADD7"><path d="M1 2h10v6H5l-3 2V8H1z"/></svg>How Can We Help You?</div>
  <div class="submit">SUBMIT</div>
</form>

<!-- footer -->
<div class="foot-brand abs"><span class="brand-dot"></span>Summit Carports</div>
<div class="contact" style="left:254px">
  <span class="ring"><svg width="18" height="18" viewBox="0 0 24 24" fill="none" stroke="#fff" stroke-width="1.8"><path d="M12 22s7-7 7-12a7 7 0 0 0-14 0c0 5 7 12 7 12z"/><circle cx="12" cy="10" r="2.5"/></svg></span>
  <span>Street Name, City Name<br>State Zipcode</span>
</div>
<div class="contact" style="left:524px">
  <span class="ring"><svg width="18" height="18" viewBox="0 0 24 24" fill="none" stroke="#fff" stroke-width="1.8"><path d="M5 3h4l2 5-2.5 1.5a11 11 0 0 0 6 6L16 13l5 2v4a2 2 0 0 1-2 2A17 17 0 0 1 3 5a2 2 0 0 1 2-2z"/></svg></span>
  <span>Call Us<br>555.201.4480</span>
</div>
<div class="contact" style="left:726px">
  <span class="ring"><svg width="18" height="18" viewBox="0 0 24 24" fill="none" stroke="#fff" stroke-width="1.8"><rect x="3" y="6" width="18" height="13"/><path d="M3 7l9 7 9-7"/></svg></span>
  <span>Email Us<br>hello@summitcarports.com</span>
</div>
<div class="socials abs"><span></span><span></span><span></span><span></span></div>
<div class="copyright abs">Copyright 2022 Summit Carports. All Rights Reserved.</div>

</body>
</html>
```